Tech business card design

We need an amazing business card design for our new business 'Pexla' a marketing tech startup based in Sydney, Australia. We provide an online marketplace for businesses to search and buy advertising media, connect with service providers and learn more about marketing. We wish to communicate 'cool tech', reliability and professionalism and design based around our logo.

Target Market(s)

Business Owners

Contact Information for Business Card

Name
Position
Email Address
Website
Phone Number

Font styles to use
Other font styles liked:
• Avenir & Avenir Next

Colors

Designer to choose colors to be used in the design.

```html
<!DOCTYPE html>
<html lang="en">
<head>
<meta charset="utf-8">
<title>Pexla business card</title>
<link rel="stylesheet" href="https://fonts.googleapis.com/css2?family=Nunito+Sans:wght@400;600;800;900&display=swap">
<style>
  :root {
    --navy: #161d4a;
    --navy-deep: #11173d;
    --stripe: #9a9ca6;
    --paper: #ffffff;
    --ink: #1a1a1f;
    --rule: #c9c9cf;
    --logo-light: #a7abc4;
    --stage: #e9e9ec;
  }
  * { box-sizing: border-box; margin: 0; padding: 0; }
  html, body { width: 1200px; height: 900px; overflow: hidden; }
  body {
    background: var(--stage);
    font-family: "Nunito Sans", Arial, sans-serif;
    position: relative;
  }
  .card {
    position: absolute;
    width: 540px;
    height: 310px;
    border-radius: 22px;
    overflow: hidden;
    box-shadow: 0 10px 30px rgba(0,0,0,.18);
  }
  .card--front { left: 80px; top: 110px; background: var(--paper); }
  .card--back { left: 580px; top: 480px; background: var(--navy); }

  .front-bands { position: absolute; inset: 0; }

  .holder {
    position: absolute; right: 34px; top: 14px;
    text-align: right; color: var(--paper);
  }
  .holder__name { font-weight: 800; font-size: 17px; letter-spacing: .5px; line-height: 1.1; }
  .holder__role { font-weight: 600; font-size: 13px; line-height: 1.2; }

  .wordmark {
    position: absolute;
    font-weight: 900;
    letter-spacing: -3px;
    line-height: 1;
  }
  .wordmark--front { left: 34px; top: 132px; font-size: 92px; color: var(--navy); }
  .wordmark--back {
    left: 0; right: 0; top: 92px; text-align: center;
    font-size: 132px; color: var(--logo-light); letter-spacing: -5px;
  }

  .contact {
    position: absolute; left: 40px; bottom: 22px;
    font-size: 14.5px; color: var(--ink); line-height: 1.5;
  }
  .contact__row { display: flex; align-items: center; gap: 6px; }
  .contact__row svg { width: 12px; height: 12px; fill: var(--ink); flex: none; }

  .divider {
    position: absolute; left: 218px; bottom: 24px;
    width: 1px; height: 62px; background: var(--rule);
  }
  .address {
    position: absolute; left: 236px; bottom: 52px;
    font-size: 14.5px; color: var(--ink); line-height: 1.25;
  }
</style>
</head>
<body>

<section class="card card--front" aria-label="Business card front">
  <svg class="front-bands" viewBox="0 0 540 310" preserveAspectRatio="none" aria-hidden="true">
    <path d="M0,0 H540 V74 C380,78 160,112 0,186 Z" fill="var(--stripe)"/>
    <path d="M0,0 H540 V62 C380,66 160,100 0,172 Z" fill="var(--navy)"/>
  </svg>

  <div class="holder">
    <p class="holder__name">JOHN SMITH</p>
    <p class="holder__role">Position</p>
  </div>

  <div class="wordmark wordmark--front">pexla</div>

  <div class="contact">
    <p class="contact__row">
      <svg viewBox="0 0 24 24"><path d="M6.6 10.8a15.1 15.1 0 0 0 6.6 6.6l2.2-2.2a1 1 0 0 1 1-.25 11.4 11.4 0 0 0 3.6.57 1 1 0 0 1 1 1V20a1 1 0 0 1-1 1A17 17 0 0 1 3 4a1 1 0 0 1 1-1h3.5a1 1 0 0 1 1 1c0 1.25.2 2.45.57 3.57a1 1 0 0 1-.25 1z"/></svg>
      012-345-6789
    </p>
    <p class="contact__row">
      <svg viewBox="0 0 24 24"><path d="M2 5h20v14H2z M2 5l10 8 10-8" fill="none" stroke="var(--ink)" stroke-width="2.4"/></svg>
      info@pexla.com
    </p>
    <p class="contact__row">
      <svg viewBox="0 0 24 24"><circle cx="12" cy="12" r="9.5" fill="none" stroke="var(--ink)" stroke-width="2"/><path d="M2.5 12h19M12 2.5c-5 5.5-5 13.5 0 19M12 2.5c5 5.5 5 13.5 0 19" fill="none" stroke="var(--ink)" stroke-width="1.6"/></svg>
      www.pexla.com
    </p>
  </div>

  <div class="divider" aria-hidden="true"></div>

  <div class="address">
    <p>Street Name, City Name</p>
    <p>Zipcode:012345</p>
  </div>
</section>

<section class="card card--back" aria-label="Business card back">
  <div class="wordmark wordmark--back">pexla</div>
</section>

</body>
</html>
```